Corvel Capital LLC

Need Professional Business cards for New Investment Fund

Target Market(s)

High Quality investors

Industry/Entity Type

Financial

Contact Information for Business Card

Phone Number +1 555 284 6190
Name Lukas Varenko
Title Fund Manager
email lv@FundCorvel.com
Website www.FundCorvel.com

Colors

Designer to choose colors to be used in the design.

Requirements
Must have
• Must have our Logo and all of the above. Must be made so lettering and loge can be raised

```html
<!DOCTYPE html>
<html lang="en">
<head>
<meta charset="utf-8">
<title>Quenvald Capital – Business Card</title>
<link rel="stylesheet" href="https://fonts.googleapis.com/css2?family=Open+Sans:wght@600;700&family=Roboto:wght@400&display=swap">
<style>
  :root {
    --page-bg: #e9e7e3;
    --card-bg: #f3f4f1;
    --ink-dark: #3b3f3d;
    --ink-mid: #464a48;
    --accent-green: #7cb518;
    --band-dark: #3f4440;
    --icon-cut: #f3f4f1;
  }
  * { box-sizing: border-box; margin: 0; padding: 0; }
  html, body {
    width: 1200px;
    height: 1054px;
    overflow: hidden;
    background: var(--page-bg);
  }
  .business-card {
    position: absolute;
    left: 172px;
    top: 293px;
    width: 856px;
    height: 517px;
    background: var(--card-bg);
    box-shadow: 0 10px 30px rgba(0,0,0,0.12);
    overflow: hidden;
  }
  .brand-name {
    position: absolute;
    top: 123px;
    left: 0;
    width: 100%;
    height: 80px;
    line-height: 80px;
    text-align: center;
    font-family: "Open Sans", Arial, sans-serif;
    font-size: 68px;
    font-weight: 700;
    letter-spacing: 1px;
    color: var(--ink-dark);
  }
  .person-name {
    position: absolute;
    top: 290px;
    left: 0;
    width: 100%;
    height: 36px;
    line-height: 36px;
    text-align: center;
    font-family: "Open Sans", Arial, sans-serif;
    font-size: 29px;
    font-weight: 600;
    letter-spacing: 0.5px;
    color: var(--accent-green);
  }
  .person-title {
    position: absolute;
    top: 333px;
    left: 0;
    width: 100%;
    height: 28px;
    line-height: 28px;
    text-align: center;
    font-family: "Roboto", Arial, sans-serif;
    font-size: 21px;
    color: var(--ink-mid);
  }
  .contact-row {
    position: absolute;
    left: 0;
    width: 100%;
    height: 28px;
    display: flex;
    justify-content: center;
    align-items: center;
    gap: 24px;
    font-family: "Roboto", Arial, sans-serif;
    font-size: 21px;
    color: var(--ink-mid);
  }
  .contact-row.phone-row { top: 386px; }
  .contact-row.web-row { top: 420px; }
  .contact-item { display: flex; align-items: center; gap: 14px; white-space: nowrap; }
  .contact-icon { width: 20px; height: 20px; fill: var(--accent-green); flex: none; }
  .card-band {
    position: absolute;
    left: 0;
    bottom: 0;
    width: 100%;
    height: 23px;
    background: linear-gradient(90deg, var(--band-dark) 0%, var(--band-dark) 45%, var(--accent-green) 100%);
  }
</style>
</head>
<body>
  <div class="business-card">
    <div class="brand-name">QUENVALD</div>

    <div class="person-name">LUKAS VARENKO</div>
    <div class="person-title">Fund Manager</div>

    <div class="contact-row phone-row">
      <span class="contact-item">
        <svg class="contact-icon" viewBox="0 0 24 24" aria-hidden="true"><path d="M2 9c0-3 4-5 10-5s10 2 10 5v2h-5V9c-1-1-3-1.5-5-1.5S8 8 7 9v2H2z"/><path d="M5 13h14l2 7H3z"/><circle cx="12" cy="16.5" r="2" fill="var(--icon-cut)"/></svg>
        +1 555 284 6190
      </span>
    </div>

    <div class="contact-row web-row">
      <span class="contact-item">
        <svg class="contact-icon" viewBox="0 0 24 24" aria-hidden="true"><path d="M2 5h20v14H2z"/><path d="M2 5l10 8 10-8" fill="none" stroke="var(--icon-cut)" stroke-width="1.6"/></svg>
        lv@FundCorvel.com
      </span>
      <span class="contact-item">
        <svg class="contact-icon" viewBox="0 0 24 24" aria-hidden="true"><circle cx="12" cy="12" r="10"/><path d="M2 12h20M12 2c3 3 3 17 0 20M12 2c-3 3-3 17 0 20" fill="none" stroke="var(--icon-cut)" stroke-width="1.4"/></svg>
        www.FundCorvel.com
      </span>
    </div>

    <div class="card-band"></div>
  </div>
</body>
</html>
```